Business Card Design

Business Card for professional consulting firm working with large financial institutions.

Target Market(s)

Executive buyers

Industry/Entity Type

Banking

Contact Information for Business Card

Mild creativity wanted. Not boring, but do elaborate artwork.

Font styles to use
Serif
Sans Serif

Colors

Designer to choose colors to be used in the design.

Requirements
Must have
• Standard business card features - company name, individual name, telephone, website, email, locations.
Nice to have
• Two colors
Should not have
• too many colors, fancy printing, cartoons.

```html
<!DOCTYPE html>
<html lang="en">
<head>
<meta charset="utf-8">
<title>Norvale Business Card</title>
<link rel="stylesheet" href="https://fonts.googleapis.com/css2?family=Roboto:wght@400&family=Roboto+Slab:wght@400;700&display=swap">
<style>
  :root {
    --backdrop: #e4e4e4;
    --card-white: #f4f4f4;
    --tab-grey: #a8a8a8;
    --band-black: #000000;
    --back-grey: #a6a6a6;
    --ink: #1e1e1e;
    --light: #ffffff;
    --title-light: #f0f0f0;
  }
  * { margin: 0; padding: 0; box-sizing: border-box; }
  html, body {
    width: 1200px;
    height: 960px;
    overflow: hidden;
    background: var(--backdrop);
  }
  .canvas {
    position: relative;
    width: 1200px;
    height: 960px;
  }
  .card {
    position: absolute;
    width: 600px;
    height: 343px;
    overflow: hidden;
  }
  .card-front { left: 314px; top: 113px; background: var(--card-white); }
  .card-back { left: 311px; top: 472px; background: var(--back-grey); }

  .brand-name {
    position: absolute;
    left: 346px;
    top: 62px;
    font-family: "Roboto Slab", Georgia, serif;
    font-weight: 400;
    font-size: 30px;
    color: var(--ink);
    letter-spacing: 0.2px;
  }

  .name-tab {
    position: absolute;
    left: 0;
    top: 164px;
    width: 600px;
    height: 75px;
  }
  .name-tab path { fill: var(--tab-grey); }

  .person {
    position: absolute;
    left: 35px;
    top: 180px;
    font-family: "Roboto Slab", Georgia, serif;
  }
  .person-name {
    font-weight: 700;
    font-size: 21px;
    color: var(--light);
    letter-spacing: 0.5px;
    line-height: 26px;
  }
  .person-title {
    font-weight: 400;
    font-size: 13px;
    color: var(--title-light);
    letter-spacing: 0.6px;
    line-height: 18px;
  }

  .contact-band {
    position: absolute;
    left: 0;
    top: 238px;
    width: 600px;
    height: 105px;
    background: var(--band-black);
    font-family: "Roboto", Arial, sans-serif;
    font-size: 14px;
    color: var(--light);
  }
  .contact-list {
    position: absolute;
    left: 35px;
    top: 24px;
    list-style: none;
  }
  .contact-list li {
    display: flex;
    align-items: center;
    height: 19.5px;
  }
  .contact-list svg {
    width: 13px;
    height: 13px;
    margin-right: 8px;
    fill: var(--light);
  }
  .address {
    position: absolute;
    right: 32px;
    top: 44px;
    text-align: right;
    font-style: normal;
    line-height: 19.5px;
  }

  .back-mark {
    position: absolute;
    right: 58px;
    bottom: 46px;
    font-family: "Roboto Slab", Georgia, serif;
    font-weight: 400;
    font-size: 44px;
    color: var(--band-black);
  }
</style>
</head>
<body>
<main class="canvas">
  <section class="card card-front">
    <div class="brand-name">norvale</div>

    <svg class="name-tab" viewBox="0 0 600 75" aria-hidden="true">
      <path d="M0 0 H220 C262 0 262 74 316 74 H0 Z"/>
    </svg>

    <div class="person">
      <div class="person-name">DANIEL REEVE</div>
      <div class="person-title">CEO/FOUNDER</div>
    </div>

    <div class="contact-band">
      <ul class="contact-list">
        <li>
          <svg viewBox="0 0 24 24" aria-hidden="true"><path d="M6.6 10.8a15.1 15.1 0 0 0 6.6 6.6l2.2-2.2c.3-.3.7-.4 1-.2 1.1.4 2.3.6 3.6.6.6 0 1 .4 1 1V20c0 .6-.4 1-1 1C10.6 21 3 13.4 3 4c0-.6.4-1 1-1h3.5c.6 0 1 .4 1 1 0 1.3.2 2.5.6 3.6.1.3 0 .7-.2 1z"/></svg>
          555 014 2290
        </li>
        <li>
          <svg viewBox="0 0 24 24" aria-hidden="true"><path d="M2 5h20v2l-10 6L2 7z M2 9l10 6 10-6v10H2z"/></svg>
          info@norvale.com
        </li>
        <li>
          <svg viewBox="0 0 24 24" aria-hidden="true"><path d="M12 2a10 10 0 1 0 0 20 10 10 0 0 0 0-20zm-1 17.9A8 8 0 0 1 4.1 10L9 15v1a2 2 0 0 0 2 2zm6.9-2.5A2 2 0 0 0 16 16h-1v-3a1 1 0 0 0-1-1H8v-2h2a1 1 0 0 0 1-1V7h2a2 2 0 0 0 2-2v-.4a8 8 0 0 1 2.9 12.8z"/></svg>
          www.norvale.com
        </li>
      </ul>
      <address class="address">
        1420 Harbor Street<br>
        Portland, Oregon 97201
      </address>
    </div>
  </section>

  <section class="card card-back">
    <div class="back-mark">norvale</div>
  </section>
</main>
</body>
</html>
```